Coffee and Plastics

I am looking for a completely new site that shows the products we have. Our current site is www.velmorebrothersbeans.com. We are open minded to what designers come up with. Our current site is www.velmorebrothersbeans.com. You can you the information from there to start the site. I need these tabs on the main home page. ( Home, Coffee & Tea, Condiments, and Paper and Plastics, and Contact.) You can take photos and info from my Current site. In products page.
I will be uploading info and photo for paper and plastics.
Look and feel
Each slider illustrates characteristics of the customer's brand and the style your logo design should communicate.

```html
<!DOCTYPE html>
<html lang="en">
<head>
<meta charset="utf-8">
<title>Velmore Brothers Beans</title>
<link href="https://fonts.googleapis.com/css2?family=Yanone+Kaffeesatz:wght@600;700&family=PT+Sans:wght@400;700&family=Cabin:wght@400&display=swap" rel="stylesheet">
<style>
:root{
  --page:#e8e8e8;
  --paper:#ffffff;
  --brown:#4b2e30;
  --brown-dark:#3d2527;
  --green:#9bb443;
  --ink:#2b2b2b;
  --text:#3a3a3a;
  --rule:#bdbdbd;
}
*{margin:0;padding:0;box-sizing:border-box}
html,body{width:1030px;height:1200px;overflow:hidden;background:var(--page)}
body{position:relative;font-family:"PT Sans",sans-serif;color:var(--text)}
.abs{position:absolute}
.sheet{left:162px;top:0;width:707px;height:1200px;background:var(--paper);box-shadow:0 0 4px rgba(0,0,0,.12)}
.brand{left:0;width:1030px;top:12px;text-align:center}
.brand-name{font-family:"Yanone Kaffeesatz",sans-serif;font-weight:700;font-size:26px;color:var(--brown);letter-spacing:.2px;line-height:1}
.brand-phone{font-family:"Yanone Kaffeesatz",sans-serif;font-weight:600;font-size:14px;color:var(--green);margin-top:3px}
.flourish{top:28px;width:22px;height:8px;border-radius:4px;background:var(--green)}
.nav{left:150px;top:74px;width:731px;height:50px;background:var(--brown)}
.nav-strip{left:150px;top:124px;width:731px;height:5px;background:var(--green)}
.nav-fold{top:129px}
.nav-home{left:176px;top:74px;width:87px;height:50px;background:var(--green)}
.nav-item{top:74px;height:50px;line-height:50px;color:#fff;font-size:12px;text-transform:uppercase;transform:translateX(-50%);white-space:nowrap}
.hero{left:177px;top:129px;width:673px;height:275px;background:linear-gradient(110deg,#a6774b 0%,#6b3f22 35%,#3b2215 60%,#8a5232 85%,#5b3520 100%)}
.dots{left:796px;top:377px;display:flex;gap:4px}
.dot{width:6px;height:6px;border-radius:50%;background:#fff}
.dot.on{background:var(--green)}
.h2{font-family:"Cabin",sans-serif;font-size:18px;color:var(--ink);line-height:1}
.rule{height:1px;background:var(--rule)}
.thumb{left:190px;top:471px;width:120px;height:83px;background:linear-gradient(135deg,#8a6a2a,#d8b660 50%,#7d5f22)}
.copy{font-size:9.3px;line-height:16px;color:var(--text)}
.photo{width:278px;height:153px}
.photo-coffee{left:184px;top:690px;background:linear-gradient(120deg,#5a2f1a,#8c5a3a 40%,#2e1a10 70%,#6b3a20)}
.photo-tea{left:517px;top:690px;background:linear-gradient(120deg,#e2d6c8,#a9744f 45%,#7a3f2c 60%,#c9b08a)}
.card-title{font-size:11.5px;font-weight:700;color:#444}
.btn{width:62px;height:25px;line-height:25px;text-align:center;background:var(--green);color:#fff;font-size:9.5px}
.footer{left:162px;top:1001px;width:707px;height:151px;background:var(--brown)}
.bottom{left:162px;top:1152px;width:707px;height:48px;background:var(--brown-dark)}
.tagline{left:162px;width:707px;text-align:center;color:#fff;font-size:9.5px;line-height:17px;top:1022px}
.arrow{top:1096px}
.partners{left:272px;top:1082px;display:flex;gap:6px;align-items:center}
.badge{height:38px;border-radius:6px;border:2px solid #e25a8a}
.legal{left:185px;top:1171px;color:#fff;font-size:9.5px}
.social{top:1169px;color:#fff;font-size:9.5px;font-weight:700;display:flex;align-items:center;gap:4px}
.social i{width:5px;height:5px;border-radius:50%;background:#fff;display:inline-block}
</style>
</head>
<body>
<div class="abs sheet"></div>

<header>
  <span class="abs flourish" style="left:371px" role="img" aria-label="Decorative flourish"></span>
  <span class="abs flourish" style="left:625px" role="img" aria-label="Decorative flourish"></span>
  <div class="abs brand">
    <div class="brand-name">Velmore Brothers Beans</div>
    <div class="brand-phone">1-800-555-0147</div>
  </div>
</header>

<nav>
  <div class="abs nav"></div>
  <svg class="abs nav-fold" style="left:150px" width="12" height="14"><polygon points="0,0 12,0 12,14" fill="var(--brown-dark)"/></svg>
  <svg class="abs nav-fold" style="left:869px" width="12" height="14"><polygon points="0,0 12,0 0,14" fill="var(--brown-dark)"/></svg>
  <div class="abs nav-strip"></div>
  <div class="abs nav-home"></div>
  <span class="abs nav-item" style="left:222px">Home</span>
  <span class="abs nav-item" style="left:315px">Coffee &amp; Tea</span>
  <span class="abs nav-item" style="left:428px">Condiments</span>
  <span class="abs nav-item" style="left:528px">Paper</span>
  <span class="abs nav-item" style="left:614px">Plastics</span>
  <span class="abs nav-item" style="left:709px">Contact</span>
</nav>

<section>
  <div class="abs hero" role="img" aria-label="Slide photo: burlap sack of roasted coffee beans beside a mug and a cast-iron coffee grinder"></div>
  <div class="abs dots"><span class="dot on"></span><span class="dot"></span><span class="dot"></span><span class="dot"></span></div>
</section>

<section>
  <h2 class="abs h2" style="left:189px;top:424px">Welcome to Velmore Brothers Beans</h2>
  <div class="abs rule" style="left:178px;top:451px;width:448px"></div>
  <div class="abs thumb" role="img" aria-label="Photo of a golden plastic condiment tray"></div>
  <p class="abs copy" style="left:330px;top:470px;width:508px">We are a family-owned and operated business based in Alder Springs Texas. Since the opening of Velmore Brothers Beans plant in 1995, we have become Texas' premier independently owned coffee packaging company. Our success relies solely on the principle of selling only the freshest, highest-quality in-room coffee available. Velmore Brothers packages and supplies in-room coffee, tea products, and condiments. Whether we're supplying a 50-room Hotel or a 500-room grand resort, we have the distribution capacity to fill your rooms with the most aromatic and robust coffees and teas available at competitive prices.</p>
  <p class="abs copy" style="left:190px;top:568px;width:655px">Velmore Brothers is continuously striving for ways to improve quality and product appearance to meet the highest standards in today's franchises and independent hotels. We are very aware that our success depends entirely upon maintaining our customers' confidence in our products, so we pay close attention to your needs every step of the way.</p>
</section>

<section>
  <h2 class="abs h2" style="left:188px;top:638px">Coffee &amp; Tea</h2>
  <div class="abs rule" style="left:178px;top:665px;width:279px"></div>
  <div class="abs photo photo-coffee" role="img" aria-label="Photo of a steaming coffee cup with beans and a metal scoop"></div>
  <div class="abs card-title" style="left:184px;top:863px">Consectetur adipisicing elit, sed do eiusmod tempor</div>
  <p class="abs copy" style="left:184px;top:880px;width:282px;line-height:17px">&nbsp;incididunt ut labore et dolore magna aliqua. Lorem ipsum dolor sit amet, consectetur adipisicing elit, sed do eiusmod tempor incididunt ut labore et dolore magna aliqua.</p>
  <a class="abs btn" style="left:182px;top:948px">Read More</a>

  <h2 class="abs h2" style="left:513px;top:638px">Condiments</h2>
  <div class="abs rule" style="left:513px;top:665px;width:329px"></div>
  <div class="abs photo photo-tea" role="img" aria-label="Photo of a clay teapot with loose tea leaves and a cup on a bamboo mat"></div>
  <div class="abs card-title" style="left:517px;top:863px">Consectetur adipisicing elit, sed do eiusmod tempor</div>
  <p class="abs copy" style="left:517px;top:880px;width:282px;line-height:17px">&nbsp;incididunt ut labore et dolore magna aliqua. Lorem ipsum dolor sit amet, consectetur adipisicing elit, sed do eiusmod tempor incididunt ut labore et dolore magna aliqua.</p>
  <a class="abs btn" style="left:515px;top:948px">Read More</a>
</section>

<footer>
  <div class="abs footer"></div>
  <p class="abs tagline">We guarantee all of our products will meet your level of satisfaction.<br>Serving Fine Establishments Everywhere!</p>
  <svg class="abs arrow" style="left:199px" width="16" height="16"><circle cx="8" cy="8" r="8" fill="var(--green)"/><polyline points="9.5,4.5 6,8 9.5,11.5" fill="none" stroke="var(--brown)" stroke-width="2"/></svg>
  <svg class="abs arrow" style="left:803px" width="16" height="16"><circle cx="8" cy="8" r="8" fill="var(--green)"/><polyline points="6.5,4.5 10,8 6.5,11.5" fill="none" stroke="var(--brown)" stroke-width="2"/></svg>
  <div class="abs partners" aria-label="Partner hotels">
    <span class="badge" style="width:58px;background:#3aa845"></span>
    <span class="badge" style="width:56px;background:#5a2a45"></span>
    <span class="badge" style="width:54px;background:#2b4a8a"></span>
    <span class="badge" style="width:58px;background:#2d5a3a"></span>
    <span class="badge" style="width:58px;background:#1f8a55"></span>
    <span class="badge" style="width:58px;background:#6a2a3a"></span>
    <span class="badge" style="width:38px;background:#1d6a4a"></span>
    <span class="badge" style="width:54px;background:#4a2a5a"></span>
  </div>
  <div class="abs bottom"></div>
  <p class="abs legal">Copy rights(c) 2014 &nbsp;Velmore Brothers Beans &nbsp;| &nbsp;&nbsp;All rights reserved.</p>
  <span class="abs social" style="left:746px"><i></i>Share</span>
  <span class="abs social" style="left:784px"><i></i>Follow</span>
  <span class="abs social" style="left:825px"><i></i>Connect</span>
</footer>
</body>
</html>
```